nutrition company business card

I would like to have a business card that has two sides, one being the green color from the Company name on the logo. I am open to ideas and looks that work with my logo. I like the idea of having a negative image of the tree on the green side.

For my information on the card I must have:
Megan Colbrook
415-555-0172
megancolbrook@quillpost.example

This area will need to be updated once I complete my schooling.

Reason: I need to extend my deadline by one day as I have been sick the last week and not had time to review all the new designs. Thank you.

Industry/Entity Type

Nutrition

Requirements
Must have
• I would like to have a business card that has two sides, one being the green color from the Company name on the logo. I am open to ideas and looks that work with my logo. I like the idea of having a negative image of the tree on the green side.
• For my information on the card I must have:
• Megan Colbrook
• 415-555-0172
• megancolbrook@quillpost.example
• This area will need to be updated once I complete my schooling.

```html
<!DOCTYPE html>
<html lang="en">
<head>
<meta charset="utf-8">
<title>Rooted Table – Business Card</title>
<link rel="stylesheet" href="https://fonts.googleapis.com/css2?family=Quicksand:wght@400;500;700&display=swap">
<style>
  :root {
    --brand-green: #7dc242;
    --brand-green-deep: #6cb232;
    --mark-brown: #7b6c66;
    --ink-grey: #6f6f6f;
    --faint-grey: #e6e6e6;
    --paper: #ffffff;
    --backdrop: #eeeeee;
  }
  * { margin: 0; padding: 0; box-sizing: border-box; }
  html, body {
    width: 1200px;
    height: 1024px;
    overflow: hidden;
    background: var(--backdrop);
    font-family: "Quicksand", sans-serif;
  }
  .sheet {
    position: relative;
    width: 1200px;
    height: 1024px;
  }
  .card {
    position: absolute;
    left: 220px;
    width: 760px;
    height: 434px;
    border-radius: 28px;
    overflow: hidden;
    box-shadow: 0 6px 18px rgba(0,0,0,0.12);
  }
  .card--front { top: 60px; background: var(--paper); }
  .card--back  { top: 542px; background: var(--brand-green); }

  /* front */
  .front-decoration {
    position: absolute;
    right: -40px;
    top: -160px;
    width: 320px;
    height: 320px;
    border-radius: 50%;
    background: var(--faint-grey);
  }
  .front-brand {
    position: absolute;
    left: 64px;
    top: 175px;
    display: flex;
    align-items: center;
    gap: 22px;
  }
  .brand-dot {
    width: 96px;
    height: 96px;
    border-radius: 50%;
    border: 5px solid var(--mark-brown);
    background: var(--paper);
  }
  .brand-name {
    font-weight: 500;
    font-size: 46px;
    line-height: 1;
    color: var(--brand-green);
  }
  .brand-tagline {
    margin-top: 6px;
    font-weight: 400;
    font-size: 22px;
    letter-spacing: 1.5px;
    color: var(--ink-grey);
  }
  .contact {
    position: absolute;
    left: 64px;
    top: 300px;
  }
  .contact-name {
    font-weight: 700;
    font-size: 24px;
    color: var(--brand-green);
    margin-bottom: 8px;
  }
  .contact-line {
    display: flex;
    align-items: center;
    gap: 10px;
    font-weight: 500;
    font-size: 22px;
    color: var(--ink-grey);
    line-height: 1.5;
  }
  .contact-line svg { width: 18px; height: 18px; flex: none; }

  /* back */
  .back-brand {
    position: absolute;
    inset: 0;
    display: flex;
    flex-direction: column;
    align-items: center;
    justify-content: center;
    color: var(--paper);
  }
  .back-brand .brand-dot {
    width: 120px;
    height: 120px;
    border: 5px solid var(--paper);
    background: transparent;
    margin-top: 18px;
    order: 3;
  }
  .back-brand .brand-name { color: var(--paper); font-size: 52px; }
  .back-brand .brand-tagline { color: var(--paper); font-size: 24px; }
</style>
</head>
<body>
<main class="sheet">

  <section class="card card--front" aria-label="Card front">
    <div class="front-decoration" aria-hidden="true"></div>

    <div class="front-brand">
      <div class="brand-dot" aria-hidden="true"></div>
      <div>
        <div class="brand-name">Rooted Table</div>
        <div class="brand-tagline">good food for busy homes</div>
      </div>
    </div>

    <div class="contact">
      <div class="contact-name">Megan Colbrook</div>
      <div class="contact-line">
        <svg viewBox="0 0 24 24" aria-hidden="true"><path fill="var(--brand-green)" d="M6.6 10.8a15.2 15.2 0 0 0 6.6 6.6l2.2-2.2c.3-.3.7-.4 1-.2 1.1.4 2.3.6 3.6.6.6 0 1 .4 1 1V20c0 .6-.4 1-1 1A17 17 0 0 1 3 4c0-.6.4-1 1-1h3.5c.6 0 1 .4 1 1 0 1.3.2 2.5.6 3.6.1.3 0 .7-.2 1z"/></svg>
        <span>415-555-0172</span>
      </div>
      <div class="contact-line">
        <svg viewBox="0 0 24 24" aria-hidden="true"><rect x="2" y="5" width="20" height="14" rx="1" fill="var(--brand-green)"/><path d="M3 6l9 7 9-7" fill="none" stroke="#fff" stroke-width="1.6"/></svg>
        <span>megancolbrook@quillpost.example</span>
      </div>
    </div>
  </section>

  <section class="card card--back" aria-label="Card back">
    <div class="back-brand">
      <div class="brand-name">Rooted Table</div>
      <div class="brand-tagline">good food for busy homes</div>
      <div class="brand-dot" aria-hidden="true"></div>
    </div>
  </section>

</main>
</body>
</html>
```